Business Card Design

I already have a company logo for my company. I have a logo for the manufacturer we represent. I want a professional business card design.

```html
<!DOCTYPE html>
<html lang="en">
<head>
<meta charset="utf-8">
<title>Alertline Services LLC – Business Card</title>
<link rel="stylesheet" href="https://fonts.googleapis.com/css2?family=Open+Sans:wght@400;600;800&display=swap">
<style>
  :root {
    --canvas: #2a2a2d;
    --card: #1e1d21;
    --card-deep: #18171b;
    --red: #e31e26;
    --gold: #c9972a;
    --white: #f4f4f4;
    --muted: #e6e6e6;
  }
  * { box-sizing: border-box; margin: 0; padding: 0; }
  html, body {
    width: 1200px; height: 780px; overflow: hidden;
    background: var(--canvas);
    font-family: "Open Sans", Arial, sans-serif;
  }
  .sheet {
    width: 1200px; height: 780px;
    display: flex; align-items: center; justify-content: center; gap: 40px;
  }
  .card {
    position: relative;
    width: 560px; height: 320px;
    border-radius: 24px;
    background: var(--card);
    border: 3px solid var(--red);
    overflow: hidden;
    box-shadow: 0 18px 40px rgba(0,0,0,.45);
  }
  /* front */
  .card-front__texture {
    position: absolute; inset: 0;
    background: radial-gradient(ellipse at 50% 45%, #2a292e 0%, var(--card) 55%, var(--card-deep) 100%);
  }
  .wordmark {
    position: absolute;
    display: flex; align-items: center; gap: 14px;
    color: var(--white);
    font-weight: 800;
    text-transform: uppercase;
    line-height: 1.05;
    letter-spacing: 1px;
  }
  .wordmark__dot {
    flex: none;
    border-radius: 50%;
    background: var(--red);
  }
  .card-front .wordmark { left: 50%; top: 50%; transform: translate(-50%, -50%); font-size: 34px; }
  .card-front .wordmark__dot { width: 46px; height: 46px; }
  .wordmark__llc { display: block; font-size: .42em; letter-spacing: 6px; }

  /* back */
  .card-back .wordmark { left: 34px; top: 104px; font-size: 22px; gap: 10px; }
  .card-back .wordmark__dot { width: 30px; height: 30px; }
  .divider {
    position: absolute; left: 238px; top: 42px;
    width: 2px; height: 176px; background: var(--gold);
  }
  .contact { position: absolute; left: 262px; top: 40px; color: var(--muted); }
  .contact__name { font-size: 25px; font-weight: 800; line-height: 1.1; }
  .contact__first { color: var(--red); }
  .contact__last { color: var(--gold); }
  .contact__role { font-size: 13px; font-weight: 600; color: var(--white); margin-top: 4px; }
  .contact__address { font-size: 13px; line-height: 1.4; margin-top: 12px; }
  .contact__list { list-style: none; margin-top: 12px; font-size: 13px; line-height: 1.6; }
  .contact__list li { display: flex; align-items: center; gap: 8px; }
  .contact__icon { width: 14px; height: 14px; flex: none; }
  .bands { position: absolute; left: 0; bottom: 0; width: 560px; height: 320px; }
</style>
</head>
<body>
<main class="sheet">

  <section class="card card-front" aria-label="Card front">
    <div class="card-front__texture" role="img" aria-label="Subtle repeating embossed pattern across the dark card face"></div>
    <div class="wordmark">
      <span class="wordmark__dot"></span>
      <span>Alertline<br>Services<span class="wordmark__llc">LLC</span></span>
    </div>
  </section>

  <section class="card card-back" aria-label="Card back">
    <div class="wordmark">
      <span class="wordmark__dot"></span>
      <span>Alertline<br>Services<span class="wordmark__llc">LLC</span></span>
    </div>

    <span class="divider"></span>

    <div class="contact">
      <p class="contact__name"><span class="contact__first">Marta</span> <span class="contact__last">Kovalenko</span></p>
      <p class="contact__role">Managing Director</p>
      <p class="contact__address">1840 Ridgeway Ave. Suite<br>310 Denton, TX 76201</p>
      <ul class="contact__list">
        <li>
          <svg class="contact__icon" viewBox="0 0 24 24" aria-hidden="true"><path fill="var(--red)" d="M6.6 10.8a15.1 15.1 0 0 0 6.6 6.6l2.2-2.2a1 1 0 0 1 1-.25 11.4 11.4 0 0 0 3.6.57 1 1 0 0 1 1 1V20a1 1 0 0 1-1 1A17 17 0 0 1 3 4a1 1 0 0 1 1-1h3.5a1 1 0 0 1 1 1c0 1.25.2 2.45.57 3.57a1 1 0 0 1-.25 1z"/></svg>
          (940) 555-0147
        </li>
        <li>
          <svg class="contact__icon" viewBox="0 0 24 24" aria-hidden="true"><rect x="2" y="5" width="20" height="14" rx="2" fill="var(--red)"/><path d="M3 6l9 7 9-7" fill="none" stroke="var(--card)" stroke-width="2"/></svg>
          hello@alertline.example
        </li>
        <li>
          <svg class="contact__icon" viewBox="0 0 24 24" aria-hidden="true"><circle cx="12" cy="12" r="10" fill="var(--red)"/><path d="M2 12h20M12 2c3 3 3 17 0 20M12 2c-3 3-3 17 0 20" fill="none" stroke="var(--card)" stroke-width="1.5"/></svg>
          www.alertline.example
        </li>
      </ul>
    </div>

    <svg class="bands" viewBox="0 0 560 320" aria-hidden="true">
      <polygon fill="var(--gold)" points="380,238 560,238 560,258 356,258"/>
      <polygon fill="var(--red)" points="0,276 322,276 350,252 376,252 336,298 0,298"/>
    </svg>
  </section>

</main>
</body>
</html>
```